Redesign of business card for Cedar Ridge Mechanical

We are looking for a new design for our business cards for Cedar Ridge Mechanical. We are a plumbing & HVAC construction company, operating on the West Coast of Canada and USA. Logo attached.
Industry/Entity Type
Construction - Plumbing & HVAC
Contact Information for Business Card
Name, address, phone numbers, email, website address
Look and feel
Each slider illustrates characteristics of the customer's brand and the style your logo design should communicate.

```html
<!DOCTYPE html>
<html lang="en">
<head>
<meta charset="utf-8">
<title>Cedar Ridge Mechanical – Business Card</title>
<link rel="stylesheet" href="https://fonts.googleapis.com/css2?family=Montserrat:wght@400;500;700;800&display=swap">
<style>
  :root {
    --backdrop: #141414;
    --card: #1c1c1c;
    --ink: #ffffff;
    --ink-soft: #d9d9d9;
    --accent-grey: #9a9a9a;
  }
  * { margin: 0; padding: 0; box-sizing: border-box; }
  html, body { width: 1200px; height: 963px; overflow: hidden; }
  body {
    background: var(--backdrop);
    font-family: "Montserrat", sans-serif;
    display: flex; align-items: center; justify-content: center;
  }
  .card {
    position: relative;
    width: 840px; height: 480px;
    background: var(--card);
    border-radius: 26px;
    overflow: hidden;
    color: var(--ink);
  }
  .brand {
    position: absolute; left: 60px; top: 70px;
    display: flex; align-items: center; gap: 16px;
  }
  .brand-square { width: 34px; height: 34px; background: var(--ink); }
  .brand-name {
    font-weight: 800; font-size: 30px; letter-spacing: 1px;
    text-transform: uppercase; line-height: 1.15; color: var(--ink);
  }
  .address {
    position: absolute; left: 60px; top: 222px;
    font-size: 20px; color: var(--ink-soft);
  }
  .divider {
    position: absolute; left: 60px; top: 262px;
    width: 620px; height: 2px; background: var(--ink);
  }
  .contacts {
    position: absolute; left: 60px; top: 284px;
    font-size: 20px; color: var(--ink-soft);
    display: flex; flex-direction: column; gap: 12px;
  }
  .contact-row { display: flex; align-items: center; gap: 10px; }
  .contact-row + .contact-row { gap: 10px; }
  .contact-row svg { width: 18px; height: 18px; fill: var(--ink); flex: none; }
  .web { margin-left: 26px; display: flex; align-items: center; gap: 10px; }
  .person {
    position: absolute; right: 60px; top: 200px; text-align: right;
  }
  .person-name { font-weight: 700; font-size: 28px; letter-spacing: 1px; text-transform: uppercase; }
  .person-role { font-size: 20px; color: var(--ink-soft); margin-top: 2px; }
  .edge-band { position: absolute; left: 0; bottom: 0; width: 100%; height: 20px; }
  .edge-notch { position: absolute; right: 0; top: 328px; width: 26px; height: 40px; background: var(--ink); }
</style>
</head>
<body>
  <article class="card">
    <div class="brand">
      <span class="brand-square"></span>
      <span class="brand-name">Cedar Ridge<br>Mechanical</span>
    </div>

    <p class="address">Your address, city, state, ZIP 0000</p>
    <div class="divider"></div>

    <div class="contacts">
      <div class="contact-row">
        <svg viewBox="0 0 24 24"><path d="M6.6 10.8a15 15 0 0 0 6.6 6.6l2.2-2.2a1 1 0 0 1 1-.25 11.4 11.4 0 0 0 3.6.57 1 1 0 0 1 1 1V20a1 1 0 0 1-1 1A17 17 0 0 1 3 4a1 1 0 0 1 1-1h3.5a1 1 0 0 1 1 1c0 1.25.2 2.45.57 3.57a1 1 0 0 1-.25 1z"/></svg>
        <span>123-456-2100</span>
      </div>
      <div class="contact-row">
        <svg viewBox="0 0 24 24"><path d="M2 5h20v14H2zm2 2v.5l8 5 8-5V7zm0 2.8V17h16V9.8l-8 5z"/></svg>
        <span>youremail@example.com</span>
        <span class="web">
          <svg viewBox="0 0 24 24"><circle cx="12" cy="12" r="10"/></svg>
          <span>www.yourwebsite.com</span>
        </span>
      </div>
    </div>

    <div class="person">
      <p class="person-name">Daniel Brooks</p>
      <p class="person-role">Manager</p>
    </div>

    <svg class="edge-band" viewBox="0 0 840 20" preserveAspectRatio="none">
      <polygon points="0,0 360,0 380,20 0,20" fill="var(--accent-grey)"/>
      <polygon points="0,6 350,6 364,20 0,20" fill="var(--ink)"/>
    </svg>
    <div class="edge-notch"></div>
  </article>
</body>
</html>
```